Corvel Capital LLC

Need Professional Business cards for New Investment Fund

Target Market(s)

High Quality investors

Industry/Entity Type

Financial

Contact Information for Business Card

Phone Number +1 555 284 6190
Name Lukas Varenko
Title Fund Manager
email lv@FundCorvel.com
Website www.FundCorvel.com

Colors

Designer to choose colors to be used in the design.

Requirements
Must have
• Must have our Logo and all of the above. Must be made so lettering and loge can be raised

```html
<!DOCTYPE html>
<html lang="en">
<head>
<meta charset="utf-8">
<title>Tarnwell – Business Cards</title>
<link rel="stylesheet" href="https://fonts.googleapis.com/css2?family=Questrial&display=swap">
<style>
  :root {
    --backdrop: #161616;
    --card-top: #2b2b2b;
    --card-bottom: #1f1f1f;
    --accent-green: #2ee81c;
    --brand-grey: #9a9a9a;
    --brand-embossed: #1a1a1a;
    --ink-light: #d6d6d6;
    --ink-muted: #b4b4b4;
    --divider: #4a4a4a;
  }
  * { margin: 0; padding: 0; box-sizing: border-box; }
  html, body {
    width: 1200px;
    height: 900px;
    overflow: hidden;
    background: var(--backdrop);
    font-family: "Questrial", "Century Gothic", sans-serif;
  }
  .card-stack {
    position: absolute;
    left: 267px;
    top: 50px;
    display: flex;
    flex-direction: column;
    gap: 40px;
  }
  .business-card {
    position: relative;
    width: 665px;
    height: 380px;
    background: linear-gradient(160deg, var(--card-top), var(--card-bottom));
    border-bottom: 5px solid var(--accent-green);
    box-shadow: 0 18px 40px rgba(0,0,0,0.55);
  }
  .card-front {
    display: flex;
    align-items: center;
    justify-content: center;
  }
  .brand-name {
    font-size: 48px;
    letter-spacing: 4px;
    color: var(--brand-grey);
    text-transform: uppercase;
    white-space: nowrap;
  }
  .card-back {
    display: flex;
    align-items: center;
  }
  .back-brand {
    width: 280px;
    text-align: center;
  }
  .back-brand .brand-name {
    font-size: 34px;
    letter-spacing: 3px;
    color: var(--brand-embossed);
  }
  .vertical-divider {
    width: 1px;
    height: 150px;
    background: var(--divider);
  }
  .contact-block {
    padding-left: 44px;
    color: var(--ink-light);
  }
  .person-name {
    font-size: 27px;
    letter-spacing: 0.5px;
  }
  .person-title {
    font-size: 19px;
    color: var(--ink-muted);
    margin-bottom: 18px;
  }
  .contact-line {
    display: flex;
    align-items: center;
    gap: 12px;
    font-size: 20px;
    line-height: 30px;
    white-space: nowrap;
  }
  .contact-icon {
    width: 16px;
    height: 16px;
    flex: none;
  }
</style>
</head>
<body>
  <main class="card-stack">
    <section class="business-card card-front">
      <span class="brand-name">Tarnwell</span>
    </section>

    <section class="business-card card-back">
      <div class="back-brand">
        <span class="brand-name">Tarnwell</span>
      </div>
      <div class="vertical-divider"></div>
      <div class="contact-block">
        <p class="person-name">Lukas Varenko</p>
        <p class="person-title">Fund Manager</p>
        <p class="contact-line">
          <svg class="contact-icon" viewBox="0 0 16 16" fill="none" stroke="#b4b4b4" stroke-width="1.4">
            <path d="M4 1.5h2.5l1 3.5-1.8 1.2a8 8 0 0 0 4 4l1.2-1.8 3.5 1V12a2 2 0 0 1-2 2A11 11 0 0 1 2 3.5 2 2 0 0 1 4 1.5z"/>
          </svg>
          +1 555 284 6190
        </p>
        <p class="contact-line">
          <svg class="contact-icon" viewBox="0 0 16 16" fill="none" stroke="#b4b4b4" stroke-width="1.4">
            <rect x="1.5" y="3.5" width="13" height="9"/>
            <path d="M1.5 3.5 8 9l6.5-5.5"/>
          </svg>
          lv@FundCorvel.com
        </p>
        <p class="contact-line">
          <svg class="contact-icon" viewBox="0 0 16 16" fill="none" stroke="#b4b4b4" stroke-width="1.3">
            <circle cx="8" cy="8" r="6.5"/>
            <ellipse cx="8" cy="8" rx="3" ry="6.5"/>
            <path d="M1.5 8h13M2.5 4.8h11M2.5 11.2h11"/>
          </svg>
          www.FundCorvel.com
        </p>
      </div>
    </section>
  </main>
</body>
</html>
```